NZ First of it's kind solutions directory and marketplace for busy Mums needs a business card design

We need a business card design for our new nationwide business in NZ (long term plans to go global). We provide solutions to the everyday challenges that busy Mums face by connecting them with quality communities and suppliers of carefully selected, relevant products and services. We sell direct via our online marketplace. The final design should communicate our values of inclusivity, quality and smart solutions. Colours should incorporate our logo colour palette of #477077 and #6ba8b2. Our website is at https://www.brightnestmums.example

Target Market(s)

busy Mums, Age 28 – 50, female, income over $100K, location main centres NZ primarily but NZ wide. Is likely juggling work or career with a young family. Probably had hobbies which have fallen by the wayside.
-Wants to succeed in her chosen career without compromising on family life
-to successfully juggle her career without feeling like she is compromising her children
- Is time poor, something always has to give and it’s generally her health (she’ll stay up late, get stressed)
- probably ex corporate or professional career. Has discretional income

Industry/Entity Type

Business

Contact Information for Business Card

Lena Forbisher, Founder, BrightNestMums.example (Strapline Tap; Gather; Sorted), 47 Kowhai Terrace, Ellerslie, Auckland 1051, New Zealand. Mob: 021 483 517 Ph: +64 (0)9 571 4860

Font styles to use
Other font styles liked:
• Raleway, and/or Architects Daughter

Colors
00a990
33b8a4
86cfc6
cfeae6

Requirements
Must have
• the above details, streamline. the logo and colours associated with those logos
Should not have
• foil or metallic colours

```html
<!DOCTYPE html>
<html lang="en">
<head>
<meta charset="utf-8">
<title>BrightNestMums – Business Card</title>
<link rel="stylesheet" href="https://fonts.googleapis.com/css2?family=Roboto:wght@400;500&family=Roboto+Condensed:wght@700&display=swap">
<style>
  :root {
    --stage: #2b2b2b;
    --paper: #f1f1f1;
    --brand-deep: #477077;
    --brand-light: #6ba8b2;
    --ink-white: #ffffff;
  }
  * { margin: 0; padding: 0; box-sizing: border-box; }
  html, body {
    width: 1200px; height: 960px; overflow: hidden;
    background: var(--stage);
    font-family: "Roboto", Arial, sans-serif;
  }
  .card {
    position: absolute;
    width: 600px; height: 342px;
    overflow: hidden;
  }
  .card--front { left: 314px; top: 113px; background: var(--paper); }
  .card--back  { left: 311px; top: 472px; background: var(--brand-light); }

  .wave-band {
    position: absolute; left: 0; right: 0; top: 150px; bottom: 0;
    background: linear-gradient(180deg,
      rgba(241,241,241,0) 0px,
      var(--brand-light) 40px,
      var(--brand-deep) 72px,
      var(--brand-deep) 100%);
  }

  .brand {
    position: absolute; left: 0; right: 0; top: 72px;
    display: flex; justify-content: center; align-items: center; gap: 12px;
  }
  .brand__dot {
    width: 34px; height: 34px; border-radius: 50%;
    background: var(--brand-deep);
  }
  .brand__name {
    font-size: 34px; font-weight: 500; letter-spacing: -0.5px;
    color: var(--brand-deep);
  }

  .person { position: absolute; left: 43px; top: 284px; color: var(--ink-white); }
  .person__name {
    font-family: "Roboto Condensed", "Arial Narrow", sans-serif;
    font-weight: 700; font-size: 21px; line-height: 24px;
  }
  .person__role { font-size: 15px; line-height: 18px; margin-left: 1px; }

  .contact {
    position: absolute; right: 30px; top: 226px;
    color: var(--ink-white); font-size: 14.5px; text-align: right;
  }
  .contact__line { display: flex; justify-content: flex-end; align-items: center; height: 19px; gap: 8px; }
  .contact__icon { width: 13px; height: 13px; fill: var(--ink-white); }
  .contact__address { margin-top: 6px; line-height: 19px; }

  .back-brand {
    position: absolute; left: 0; right: 0; top: 150px;
    display: flex; justify-content: center; align-items: center; gap: 12px;
  }
  .back-brand__dot {
    width: 34px; height: 34px; border-radius: 50%;
    background: var(--ink-white);
  }
  .back-brand__name {
    color: var(--ink-white);
    font-size: 34px; font-weight: 500; letter-spacing: -0.5px;
  }
  .strapline {
    position: absolute; left: 0; right: 0; top: 305px;
    text-align: center; color: var(--ink-white); font-size: 14.5px;
  }
</style>
</head>
<body>

<section class="card card--front" aria-label="Business card front">
  <div class="wave-band" role="img" aria-label="Flowing teal and grey wave band across the lower card"></div>

  <div class="brand">
    <span class="brand__dot" aria-hidden="true"></span>
    <span class="brand__name">BrightNestMums</span>
  </div>

  <div class="person">
    <div class="person__name">LENA FORBISHER</div>
    <div class="person__role">FOUNDER</div>
  </div>

  <div class="contact">
    <div class="contact__line">+64 (0)9 571 4860
      <svg class="contact__icon" viewBox="0 0 16 16" aria-hidden="true"><path d="M3.6 1.2l2.3 2.6c.4.4.3 1-.1 1.4L4.6 6.3c.9 2 2.6 3.8 4.8 4.9l1.2-1.2c.4-.4 1-.4 1.4-.1l2.6 2.2c.4.4.5 1 .1 1.5l-1.3 1.4c-.5.5-1.3.7-2 .4C6.6 13.7 2.6 9.8.8 5 .5 4.3.7 3.5 1.2 3l1-1.4c.4-.5 1-.5 1.4-.4z"/></svg>
    </div>
    <div class="contact__line">021 483 517
      <svg class="contact__icon" viewBox="0 0 16 16" aria-hidden="true"><path d="M4 0h8c.6 0 1 .4 1 1v14c0 .6-.4 1-1 1H4c-.6 0-1-.4-1-1V1c0-.6.4-1 1-1zm1 2v11h6V2H5z"/></svg>
    </div>
    <div class="contact__line">BrightNestMums.example
      <svg class="contact__icon" viewBox="0 0 16 16" aria-hidden="true"><circle cx="8" cy="8" r="7.5"/><path d="M1 8h14M8 .5c2.5 2.5 2.5 12.5 0 15M8 .5c-2.5 2.5-2.5 12.5 0 15" stroke="var(--brand-deep)" stroke-width="1.2" fill="none"/></svg>
    </div>
    <div class="contact__address">47 Kowhai Terrace, Ellerslie<br>Auckland 1051, New Zealand</div>
  </div>
</section>

<section class="card card--back" aria-label="Business card back">
  <div class="back-brand">
    <span class="back-brand__dot" aria-hidden="true"></span>
    <span class="back-brand__name">BrightNestMums</span>
  </div>
  <div class="strapline">Tap; Gather; Sorted</div>
</section>

</body>
</html>
```